New Business Card for Odd Fern Designs

I create and make jewellery and Clothing. But when it comes to business card design I fail completely.

Sketching is my area, drawing, putting things together neatly, not so much.

Here is a little blurb about my company:

Odd Fern Designs is a truly unique customer experience. Work one on one with Owner Petra Wolcott to make your costuming dreams come true.

Not after a costume? Browse through the store for a look at beautiful and unique piece of jewellery. Each piece has been put together by Petra, by hand. You'll find Steampunk, gothic, lolita and other quirky styles.

Want something else? What abotu a pair of warm kitty paws? A Pair of Kitty ears? A pony tail to wear on your jeans? There are so many options and things to choose! You will want to take it all home.

I have attached the previous business card with my mascot "Greta" As you can see there is a very Greta in Cloudmere feel to the overall company, with references to The Tin Tinker, and the idea that "We are all made here".

Colour's to use would be purple and blue. The winning design would show the unique but professional approach that Odd Fern Designs takes when creating each piece for their customers.

Reason: Wanted to give you a chance to go over feed back that has been sent out. I am committed to paying for the design that I will use. I think another week will help tweak things up.

Target Market(s)

Nerds, Geeks and Sci-Fi people aged 20 - 34 both Male and Female

Industry/Entity Type

Store

Requirements
Must have
• Website address: www.oddferndesigns.example

Yeah, rest is up too you!
Nice to have
• Honestly, if you could make the whole thing look like a Edwin Marlowe "Greta in Cloudmere" Drawing with the same line working style that would be amazing!

But I won't restrict you! I'd like to see what you can come up with.

```html
<!DOCTYPE html>
<html lang="en">
<head>
<meta charset="utf-8">
<title>Petra Wolcott – Odd Fern Designs</title>
<link rel="stylesheet" href="https://fonts.googleapis.com/css2?family=Kavoon&display=swap">
<style>
  :root {
    --sky-deep: #04a4b7;
    --sky-mid: #34c3cf;
    --sky-pale: #a9dde3;
    --paper: #ffffff;
    --ink: #7e585b;
    --ink-soft: #c39a9c;
    --rule: #a9bcc4;
  }
  html, body {
    margin: 0;
    padding: 0;
    overflow: hidden;
  }
  .card {
    position: relative;
    width: 1200px;
    height: 667px;
    overflow: hidden;
    background: linear-gradient(180deg,
      var(--sky-deep) 0%,
      var(--sky-mid) 22%,
      var(--sky-pale) 52%,
      #e4f4f6 75%,
      var(--paper) 100%);
    font-family: "Kavoon", cursive;
    color: var(--ink);
  }
  .contact-block,
  .tagline {
    position: absolute;
    right: 263px;
    text-align: right;
    white-space: nowrap;
  }
  .contact-block {
    top: 88px;
    width: 660px;
  }
  .owner-name {
    margin: 0 -10px 0 0;
    font-size: 80px;
    line-height: 100px;
    font-weight: 400;
    letter-spacing: 10px;
  }
  .divider {
    height: 1px;
    margin: 10px 0 16px;
    background: var(--rule);
    border: 0;
  }
  .email,
  .website {
    display: block;
    font-size: 39px;
    line-height: 68px;
  }
  .email {
    letter-spacing: 1.8px;
    margin-right: -1.8px;
  }
  .website {
    color: var(--ink-soft);
    letter-spacing: 2.9px;
    margin-right: -2.9px;
  }
  .tagline {
    top: 385px;
    margin: 0;
    font-size: 98px;
    line-height: 100px;
    font-weight: 400;
  }
  .tagline span {
    display: block;
  }
</style>
</head>
<body>
  <main class="card">
    <section class="contact-block">
      <h1 class="owner-name">Petra Wolcott</h1>
      <hr class="divider">
      <span class="email">hello@oddferndesigns.example</span>
      <span class="website">www.oddferndesigns.example</span>
    </section>
    <p class="tagline">
      <span>Small-batch</span>
      <span>odd little joys</span>
    </p>
  </main>
</body>
</html>
```